Food Safety 1-California workers only

3.25" by 4.5" Black and White Magazine Ad
This ad is to train California workers only.
Workers will be trained on: Food Safety, FSMA (Food Safety Modernization Act), using equipment safety, food processing production skills, worker safety, supervisory skills, communication skills.
"FREE TRAINING", The company does the training or Harrowgate Instruction will provide the training.
Training grants range from $100,000 to $400,000.
Companies must be in business for profit.
Companies must train 200 employees or more.
This program is for California workers only.
Incumbent or new-hires are eligible.

Target Market(s)

California food processors, farms, food packaging, food processors, companies under FSMA, food safety, food production who need to train employees.

Industry/Entity Type

Food Production

Font styles to use
Serif
Sans Serif

Colors

Designer to choose colors to be used in the design.

Requirements
Must have
• This is a 3.25 inch by 4.5 inch magazine ad. It must be black and white. No color.
• The deliverable must be in basic PhotoShop. The ad does not need to include any graphics and be text only if needed. If you have a black and white graphic that will show well.
• Look at www.HGIPlateWatch..example
• Use the text from "TRAVO7-Photoshop-052018" file as your starting point.
Nice to have
• A black and white graphic about food. See www.HGIPlateWatch.example
Should not have
• No color.

```html
<!DOCTYPE html>
<html lang="en">
<head>
<meta charset="utf-8">
<title>Food Safety Training Ad</title>
<link href="https://fonts.googleapis.com/css2?family=Montserrat:wght@200;300;700;800&family=Open+Sans:wght@400;600&family=Libre+Baskerville:wght@400;700&display=swap" rel="stylesheet">
<style>
  :root {
    --page: #e9e9e9;
    --ink-deep: #1c1c1c;
    --ink-dark: #2e2e2e;
    --ink-mid: #4a4a4a;
    --paper: #ffffff;
    --text-light: #f2f2f2;
    --text-soft: #d6d6d6;
    --text-body: #3a3a3a;
    --photo-a: #9a9a9a;
    --photo-b: #3c3c3c;
  }
  * { margin: 0; padding: 0; box-sizing: border-box; }
  html, body { width: 1200px; height: 1200px; overflow: hidden; background: var(--page); }
  .ad {
    position: absolute; left: 195px; top: 40px; width: 810px; height: 1120px;
    background: radial-gradient(ellipse at 30% 15%, var(--ink-mid), var(--ink-dark) 55%, var(--ink-deep));
    overflow: hidden; font-family: "Montserrat", sans-serif; color: var(--text-light);
    box-shadow: 0 6px 24px rgba(0,0,0,.25);
  }
  .ad-title { position: absolute; left: 40px; right: 40px; top: 44px; font-size: 84px; line-height: 1; letter-spacing: 1px; white-space: nowrap; text-align: center; }
  .ad-title .light { font-weight: 200; }
  .ad-title .bold { font-weight: 800; }
  .topic-list { position: absolute; right: 40px; top: 158px; text-align: right; }
  .topic-list .act { font-weight: 700; font-size: 25px; letter-spacing: .5px; }
  .topic-list .skill { font-weight: 700; font-size: 32px; margin-top: 6px; }
  .slogan {
    position: absolute; right: 40px; top: 300px; background: #111; padding: 12px 24px;
    font-weight: 700; font-size: 22px; line-height: 1.25; text-align: center; text-transform: uppercase;
  }
  .art { position: absolute; inset: 0; }
  .contact { position: absolute; left: 40px; top: 780px; width: 340px; }
  .contact .name { font-family: "Libre Baskerville", serif; font-weight: 700; font-size: 32px; }
  .contact .company { font-family: "Libre Baskerville", serif; font-size: 14px; color: var(--text-soft); margin-bottom: 12px; }
  .contact-row { display: flex; gap: 16px; align-items: flex-start; font-family: "Open Sans", sans-serif; font-size: 18px; color: var(--text-soft); margin-top: 12px; line-height: 1.3; }
  .contact-row svg { flex: none; width: 22px; height: 22px; margin-top: 2px; }
  .qualify { position: absolute; left: 430px; top: 795px; width: 350px; color: var(--text-body); }
  .qualify h2 { font-family: "Libre Baskerville", serif; font-weight: 700; font-size: 19px; text-decoration: underline; margin-bottom: 8px; }
  .qualify ul { font-family: "Open Sans", sans-serif; font-size: 18px; line-height: 1.35; padding-left: 22px; }
</style>
</head>
<body>
<main class="ad">
  <svg class="art" viewBox="0 0 810 1120" width="810" height="1120">
    <defs>
      <radialGradient id="photoTone" cx="40%" cy="35%" r="70%">
        <stop offset="0" stop-color="var(--photo-a)"/>
        <stop offset="1" stop-color="var(--photo-b)"/>
      </radialGradient>
      <linearGradient id="panelFade" x1="0" y1="0" x2="0" y2="1">
        <stop offset="0" stop-color="#2a2a2a" stop-opacity="0"/>
        <stop offset="1" stop-color="#5a5a5a"/>
      </linearGradient>
    </defs>
    <rect x="0" y="740" width="400" height="380" fill="url(#panelFade)"/>
    <path class="qualify-panel" d="M400 1120 L400 800 Q440 725 560 720 L810 720 L810 1120 Z" fill="var(--paper)"/>
    <circle role="img" aria-label="Overhead photo of a plated meal with sliced chicken, avocado, grains and tomatoes" cx="230" cy="540" r="190" fill="url(#photoTone)" stroke="#111" stroke-width="6"/>
    <circle role="img" aria-label="Photo of a heap of assorted fresh fruit and vegetables" cx="640" cy="560" r="140" fill="url(#photoTone)" stroke="#111" stroke-width="6"/>
    <circle role="img" aria-label="Photo of a fresh side salad" cx="440" cy="690" r="78" fill="url(#photoTone)" stroke="#111" stroke-width="6"/>
  </svg>

  <h1 class="ad-title"><span class="light">FOOD </span><span class="bold">SAFETY</span></h1>
  <div class="topic-list">
    <p class="act">FOOD SAFETY MODERNIZATION ACT</p>
    <p class="skill">Production Skills</p>
    <p class="skill">Worker Safety</p>
  </div>
  <p class="slogan">“We do the training and<br>the state pays for it!”</p>

  <section class="contact">
    <p class="name">Martin Hale</p>
    <p class="company">(Harrowgate Instruction Company, Inc.)</p>
    <div class="contact-row">
      <svg viewBox="0 0 24 24"><path d="M6 3l3 0 1.5 4-2 1.5a11 11 0 0 0 7 7l1.5-2 4 1.5v3a2 2 0 0 1-2 2A17 17 0 0 1 4 5a2 2 0 0 1 2-2z" fill="none" stroke="currentColor" stroke-width="1.8"/></svg>
      <span>(555) 014-2280</span>
    </div>
    <div class="contact-row">
      <svg viewBox="0 0 24 24" fill="none" stroke="currentColor" stroke-width="1.6"><circle cx="12" cy="12" r="9"/><ellipse cx="12" cy="12" rx="4" ry="9"/><path d="M3 12h18M5 7h14M5 17h14"/></svg>
      <span>www.HGIPlateWatch.example<br>www.HGICAL.example</span>
    </div>
    <div class="contact-row">
      <svg viewBox="0 0 24 24"><rect x="3" y="6" width="18" height="12" fill="currentColor"/><path d="M3 6l9 7 9-7" fill="none" stroke="#333" stroke-width="1.6"/></svg>
      <span>M.Hale@HGICAL.example</span>
    </div>
    <div class="contact-row">
      <svg viewBox="0 0 24 24"><path d="M12 2a7 7 0 0 0-7 7c0 5 7 13 7 13s7-8 7-13a7 7 0 0 0-7-7z" fill="currentColor"/><circle cx="12" cy="9" r="2.5" fill="#333"/></svg>
      <span>1200 Linden Court<br>Suite 310<br>Fairview, CA 90000</span>
    </div>
  </section>

  <section class="qualify">
    <h2>How to Qualify:</h2>
    <ul>
      <li>Train California Workers Only</li>
      <li>Trainees must earn $11/hour</li>
      <li>Full-time workers only</li>
      <li>Employees must attend at least 8 Hours of training</li>
      <li>You must train 200 or more employees</li>
      <li>Incumbent or New-Hire workers are eligible</li>
      <li>Seasonal workers are eligible</li>
    </ul>
  </section>
</main>
</body>
</html>
```